GUARD AGAINST CLAIMS

I'm virtually ready to launch my site, but I have a number of edits and modifications that need to be implemented. More importantly, I'm always looking to improve my site, particularly now that I am making my proverbial "FIRST IMPRESSION." Thus, I'm willing to see if there is someone who can add creativity and perhaps improve what I already have, particularly on the All Important Front Page.

```html
<!DOCTYPE html>
<html lang="en">
<head>
<meta charset="utf-8">
<title>Guard Against Claims</title>
<link href="https://fonts.googleapis.com/css2?family=Poppins:wght@300;400;500;600;700&display=swap" rel="stylesheet">
<style>
:root{
  --navy:#0b2250;
  --navy-mid:#163a78;
  --red:#c4121c;
  --pale:#eef2f8;
  --ink:#1b2440;
  --muted:#4a5470;
  --white:#ffffff;
}
*{box-sizing:border-box;margin:0;padding:0}
html,body{width:1200px;height:4062px;overflow:hidden}
body{position:relative;font-family:'Poppins',sans-serif;background:var(--pale);color:var(--ink)}
.abs{position:absolute}
.stars{letter-spacing:3px;font-size:16px;color:var(--navy);text-align:center}
.stars.light{color:var(--white)}
.section-title{font-weight:700;font-size:21px;text-align:center;color:var(--navy)}

/* hero */
.hero{left:0;top:0;width:1200px;height:675px;background:linear-gradient(160deg,#2a2320 0%,#5a4330 35%,#3b2c22 60%,#1a1816 100%)}
.hero-shade{left:0;top:0;width:1200px;height:675px;background:linear-gradient(180deg,rgba(11,34,80,.2) 0%,rgba(11,34,80,0) 40%,rgba(11,34,80,.55) 100%)}
.topbar{left:0;top:40px;width:1200px;height:55px;background:rgba(11,34,80,.85)}
.brand{left:164px;top:16px;width:104px;height:104px;border-radius:50%;background:var(--red);border:5px solid var(--white);display:flex;align-items:center;justify-content:center;color:var(--white);font-weight:700;font-size:26px}
.top-address{left:285px;top:50px;font-size:11.5px;line-height:16px;color:var(--white);font-weight:500}
.top-call{left:735px;top:59px;font-size:12.5px;color:var(--white);font-weight:500}
.top-call b{color:var(--red);font-weight:600}
.menu-icon{left:1012px;top:58px}
.hero-tag{left:164px;top:407px;background:var(--navy);color:var(--white);font-size:12.5px;font-weight:600;padding:3px 8px}
.hero-title{left:162px;top:426px;color:var(--white);font-weight:600;font-size:35px}
.hero-lead{left:162px;top:474px;width:860px;color:var(--white);font-size:12px;font-weight:600;line-height:18.5px}
.hero-cta-text{left:160px;top:563px;color:var(--white);font-size:17px;line-height:22px}
.btn-red{background:var(--red);color:var(--white);font-weight:600;font-size:13px;display:flex;align-items:center;justify-content:center}
.hero-btn{left:629px;top:568px;width:262px;height:44px}
.hero-more{left:902px;top:568px;width:136px;height:44px;border:1.5px solid var(--white);color:var(--white);font-size:12px;display:flex;align-items:center;justify-content:center;gap:10px}
.pause{left:1152px;top:623px;width:34px;height:34px;border:2px solid var(--white);border-radius:50%;opacity:.8}

/* about */
.about{left:0;top:675px;width:1200px;height:680px;background:linear-gradient(180deg,var(--navy) 0%,var(--navy-mid) 28%,rgba(22,58,120,.25) 45%,var(--pale) 55%)}
.about-text{left:162px;top:806px;width:876px;text-align:center;color:var(--white);font-size:12.5px;line-height:21px}
.plan-title{left:601px;top:890px;width:440px;color:var(--white);font-weight:700;font-size:24px;line-height:24px}
.plan-body{left:603px;top:990px;width:432px;font-size:11px;line-height:19px;color:var(--muted)}
.plan-body p{margin-bottom:19px}
.money{left:164px;top:1072px;width:139px;height:127px;background:linear-gradient(135deg,#c9cfc4,#8fa08e 50%,#5f6f66)}
.quote{left:330px;top:1094px;width:210px;font-size:13px;line-height:22px;color:var(--muted)}
.quote-by{left:330px;top:1158px;font-size:12.5px;font-weight:600;color:var(--navy)}

/* contact banner */
.rule{left:162px;top:1430px;width:876px;height:1px;background:var(--navy);opacity:.6}
.banner{left:328px;top:1407px;width:542px;height:47px}
.banner-text{left:328px;top:1407px;width:542px;height:47px;display:flex;align-items:center;justify-content:center;color:var(--white);font-size:20px}

/* practice */
.practice-intro{left:200px;top:1622px;width:800px;text-align:center;font-size:16px;line-height:25px;color:var(--muted)}
.practice-intro b{color:var(--navy)}
.card{width:281px;height:375px;text-align:center}
.card.dark{background:var(--navy);color:var(--white)}
.card.light{background:var(--white);color:var(--navy)}
.card-img{height:161px}
.card h3{font-size:17px;font-weight:700;line-height:16px;margin:20px 14px 0;height:34px;display:flex;align-items:center;justify-content:center}
.card p{font-size:10.5px;line-height:15.5px;margin:10px 20px 0;height:98px}
.card.light p{color:var(--muted)}
.pill{display:inline-block;width:106px;height:22px;line-height:22px;border-radius:11px;font-size:8.5px}
.card.dark .pill{background:var(--white);color:var(--navy)}
.card.light .pill{background:#e7ebf1;color:var(--navy)}

/* case / testimonial */
.case-title{left:163px;top:2670px;font-size:21px;font-weight:600;color:var(--navy)}
.case-cat{left:163px;top:2750px;font-size:12px;font-weight:600;color:var(--muted)}
.case-head{left:162px;top:2788px;width:360px;font-size:21px;font-weight:600;line-height:25px;color:var(--ink)}
.case-col{width:190px;font-size:11px;line-height:19px;color:var(--muted)}
.case-col b{color:var(--ink);font-weight:600}
.testi{left:621px;top:2588px;width:417px;height:467px;background:linear-gradient(180deg,#e3e8f0,#d6dde8)}
.testi-title{left:654px;top:2670px;font-size:21px;font-weight:600;color:var(--navy)}
.testi-quote{left:658px;top:2800px;width:360px;font-size:25px;line-height:28px;color:var(--navy);font-weight:400}
.testi-mark{left:660px;top:2765px;font-size:30px;color:#9aa6bb;font-style:italic}
.testi-name{left:660px;top:2979px;font-size:11px;font-weight:600;color:var(--ink)}
.testi-all{left:956px;top:2979px;font-size:11px;font-weight:600;color:var(--navy-mid)}

/* faq */
.faq{left:0;top:3154px;width:1200px;height:659px;background:linear-gradient(90deg,#c7ced9,#dfe4ec 50%,#c5ccd7)}
.acc{left:162px;width:458px;background:var(--white);border:1px solid #d4dae4;font-size:13.5px;color:var(--muted);display:flex;align-items:center;justify-content:space-between;padding:0 22px}
.acc svg{flex:none}
.acc-open{left:162px;top:3329px;width:458px;height:108px;background:#e4e8ef}
.acc-open .acc-head{background:var(--white);height:37px;display:flex;align-items:center;justify-content:space-between;padding:0 22px;font-size:13.5px;font-weight:600;color:var(--navy);border:1px solid #d4dae4}
.acc-open p{padding:12px 22px 0;font-size:10.5px;line-height:15px;color:var(--muted)}
.faq-photo{left:688px;top:3329px;width:350px;height:383px;background:linear-gradient(160deg,#6b4a36,#3a2c26 50%,#1e1a1b)}

/* footer */
.footer{left:0;top:3813px;width:1200px;height:249px;background:var(--navy)}
.f-brand{left:164px;top:3867px;width:104px;height:104px;border-radius:50%;background:var(--red);border:5px solid var(--white);display:flex;align-items:center;justify-content:center;color:var(--white);font-weight:700;font-size:26px}
.f-address{left:320px;top:3862px;width:260px;color:var(--white);font-size:11px;line-height:25px}
.f-phone{left:320px;top:3938px;color:var(--white);font-size:16.5px}
.f-nav{left:650px;top:3864px;font-size:10px;line-height:25px;color:#c9d2e4}
.f-nav b{color:var(--white);font-weight:600}
.f-legal{left:762px;top:3864px;font-size:10px;line-height:25px;color:#c9d2e4}
.social{top:3868px;width:24px;height:24px;border-radius:50%;background:var(--white)}
.f-btn{left:762px;top:3933px;width:276px;height:41px}
.copy{left:163px;top:4016px;font-size:8px;color:#8e9abb}
</style>
</head>
<body>

<!-- hero -->
<div class="abs hero" role="img" aria-label="Courtroom scene with attorneys arguing before a judge"></div>
<div class="abs hero-shade"></div>
<div class="abs topbar"></div>
<div class="abs brand">GAC</div>
<div class="abs top-address">4820 East Canyon Ridge Rd, Suite 210<br>Mesa, Arizona 85210</div>
<div class="abs top-call"><b>CALL NOW -</b> 480.555.0142 / 800.555.0199</div>
<svg class="abs menu-icon" width="24" height="18" viewBox="0 0 24 18"><g stroke="#c4121c" stroke-width="2.4"><line x1="2" y1="3" x2="22" y2="3"/><line x1="2" y1="9" x2="22" y2="9"/><line x1="2" y1="15" x2="16" y2="15"/></g></svg>
<div class="abs hero-tag">BUSINESS OWNERS:</div>
<div class="abs hero-title">Guard Against Claims (GAC)</div>
<div class="abs hero-lead">Is An Extremely Affordable Legal Service Plan (As Little As $8.00 Per Month) That INSULATES Business Owners From Unwarranted LEGAL CLAIMS And Expensive LAWSUITS. Our Plan Uses Local, Experienced, Quality Attorneys Who Focus On PROBLEM PREVENTION Using Proprietary Tools Available Only To GAC Members.</div>
<div class="abs hero-cta-text">Contact us to find out how you can join us to<br><b>GUARD AGAINST CLAIMS!!</b></div>
<div class="abs btn-red hero-btn">SCHEDULE FREE CONSULATION</div>
<div class="abs hero-more">LEARN MORE <svg width="20" height="14" viewBox="0 0 20 14"><g fill="none" stroke="#fff" stroke-width="1.6"><path d="M12 1H2v12h10"/><path d="M8 7h11M15 3l4 4-4 4"/></g></svg></div>
<div class="abs pause"><svg width="30" height="30" viewBox="0 0 30 30"><g stroke="#fff" stroke-width="2"><line x1="12" y1="10" x2="12" y2="20"/><line x1="18" y1="10" x2="18" y2="20"/></g></svg></div>

<!-- about -->
<div class="abs about"></div>
<div class="abs stars light" style="left:0;top:716px;width:1200px">★★★</div>
<div class="abs section-title" style="left:0;top:750px;width:1200px;color:#fff">ABOUT US</div>
<div class="abs about-text">GAC is a group of attorney and legal assistants with many years of experience in litigation, who are devoted to PREVENTING LEGAL CLAIMS and COSTLY LAWSUITS through a variety of FREE and VERY AFFORDABLE services described below.</div>
<div class="abs plan-title">OUR UNIQUE SERVICE PLAN MAKES IT POSSIBLE FOR US TO GUARD AGAINST CLAIMS.</div>
<div class="abs plan-body">
  <p>A homebuilding company was sued by a former employee who claimed to have been promised a more favorable sales area, which claim was disputed by the homebuilder. There was no evidence that such a promise had been made, other than the plaintiff's oral testimony. The company had the case dismissed, but spent $10,000 defending the case.</p>
  <p>And even though it was awarded its attorney's fees, the plaintiff proved uncollectible. Had the company been an GAC member, the case likely would never have been filed. Call for your FREE CONSULTATION and let us show you why the plaintiff likely would not have found a contingency attorney (as was the case) or been able to pay an attorney on an hourly basis. In short, by using GAC's services, the plaintiff's claim would not have been filed.</p>
  <p>In our vast experience with commercial litigation, we believe that a very large percentage of litigation cases hinge on "he said / she said" issues. By using GAC's services, we believe we can INSULATE you and your business from all such issues, which will MINIMIZE your EXPOSURE to LEGAL CLAIMS and LAWSUITS.</p>
</div>
<div class="abs money" role="img" aria-label="Stack of banknotes"></div>
<div class="abs quote">- An OUNCE of PREVENTION is worth a POUND of CURE.</div>
<div class="abs quote-by">Thomas Whitfield.</div>

<!-- contact banner -->
<div class="abs rule"></div>
<svg class="abs banner" viewBox="0 0 542 47" preserveAspectRatio="none"><polygon points="14,0 528,0 542,23.5 528,47 14,47 0,23.5" fill="#0b2250"/></svg>
<div class="abs banner-text">CONTACT US FOR&nbsp;<b>A FREE CONSULTATION</b></div>

<!-- practice areas -->
<div class="abs stars" style="left:0;top:1539px;width:1200px">★★★</div>
<div class="abs section-title" style="left:0;top:1574px;width:1200px">OUR LEGAL PRACTICE AREAS</div>
<div class="abs practice-intro">The price for a membership is a ridiculously low <b>$9.95 PER WEEK</b>. We believe that this fee is very affordable. So what is it? Membership includes the following:</div>

<div class="abs card dark" style="left:162px;top:1716px">
  <div class="card-img" role="img" aria-label="Attorney reviewing documents beside scales of justice" style="background:linear-gradient(135deg,#e8e2da,#a68f75 60%,#5b4634)"></div>
  <h3>FREE INITIAL CONSULTATION</h3>
  <p>As a prospective Guard Against Claims ("GAC") member, we urge you to schedule an initial consultation with us – at no charge – where we will go over each of the services in detail, and offer an overview of your business for-mation at no charge.</p>
  <span class="pill">LEARN MORE</span>
</div>
<div class="abs card light" style="left:460px;top:1716px">
  <div class="card-img" role="img" aria-label="Gavel and brass scales on a desk" style="background:linear-gradient(135deg,#7a4a2e,#b07a4a 50%,#4a2a1a)"></div>
  <h3>PROPRIETARY CONTRACT LANGUAGE</h3>
  <p>GAC members are entitled to incorporate exclusive proprietary contract language in their contracts, work orders, and other written agreements in their business, that MINIMIZES EXPOSURE to legal claims against your business.</p>
  <span class="pill">LEARN MORE</span>
</div>
<div class="abs card dark" style="left:757px;top:1716px">
  <div class="card-img" role="img" aria-label="Hand touching a digital screen" style="background:linear-gradient(135deg,#1b3a78,#4f7ac0 50%,#0e2350)"></div>
  <h3>FREE CONSULTATION</h3>
  <p>GAC members can call their local GAC Attorney any time, and be given a 30 minute consultation, free of charge, once per month. The value of this cannot be overstated and easily pays for the membership – many times over.</p>
  <span class="pill">LEARN MORE</span>
</div>
<div class="abs card light" style="left:162px;top:2110px">
  <div class="card-img" role="img" aria-label="Businessman on the phone holding a letter" style="background:linear-gradient(135deg,#4d6a3e,#c8b49a 55%,#8a7763)"></div>
  <h3>FREE ATTORNE LETTERS</h3>
  <p>In addition to free monthly consultations, GAC members can have their GAC Attorney send out a letter regarding their business, once per month, at no charge.</p>
  <span class="pill">LEARN MORE</span>
</div>
<div class="abs card dark" style="left:460px;top:2110px">
  <div class="card-img" role="img" aria-label="Gavel resting on banknotes" style="background:linear-gradient(135deg,#8fa39a,#5e4a3a 50%,#a8b3a6)"></div>
  <h3>LITIGATION DISCOUNTS</h3>
  <p>GAC members who use the Proprietary Contract Language described above are given considerable discounts, including flat fee discounts, in the even of defensive litigation.</p>
  <span class="pill">LEARN MORE</span>
</div>
<div class="abs card light" style="left:757px;top:2110px">
  <div class="card-img" role="img" aria-label="Lawyer signing papers next to scales" style="background:linear-gradient(135deg,#d8d2c8,#8a6a48 55%,#2e2a2a)"></div>
  <h3>COLLECTIONS</h3>
  <p>GAC members can have their GAC Attorney pursue collection claims on a contingency fee basis, provided the claim is based on a contract.</p>
  <span class="pill">LEARN MORE</span>
</div>

<!-- case studies -->
<div class="abs stars" style="left:163px;top:2646px;text-align:left">★★★</div>
<div class="abs case-title">Case studies</div>
<div class="abs case-cat">Personal Injury</div>
<div class="abs case-head">Securing Justice for a Victim of Negligence</div>
<div class="abs case-col" style="left:163px;top:2864px"><b>Situation:</b> A client suffered severe injuries in a car accident due to another driver's negligence.</div>
<div class="abs case-col" style="left:379px;top:2864px"><b>Approach:</b> Our firm conducted a thorough investigation, collected evidence, and negotiated with insurance companies.</div>
<svg class="abs" style="left:162px;top:2985px" width="18" height="14" viewBox="0 0 18 14"><g fill="none" stroke="#1b2440" stroke-width="2"><path d="M17 7H2M7 1L1 7l6 6"/></g></svg>
<svg class="abs" style="left:548px;top:2985px" width="18" height="14" viewBox="0 0 18 14"><g fill="none" stroke="#1b2440" stroke-width="2"><path d="M1 7h15M11 1l6 6-6 6"/></g></svg>

<div class="abs testi" role="img" aria-label="Faint scales of justice background"></div>
<div class="abs stars" style="left:654px;top:2646px;text-align:left">★★★</div>
<div class="abs testi-title">Testimonials</div>
<div class="abs testi-mark">“</div>
<div class="abs testi-quote">Lorem ipsum dolor sit amet, consectetur adipiscing elit. Suspendisse varius enim in eros elementum tristique...</div>
<div class="abs testi-name">Morgan R, USA</div>
<div class="abs testi-all">Read All</div>

<!-- faq -->
<div class="abs faq" role="img" aria-label="Faded law library background"></div>
<div class="abs stars" style="left:0;top:3200px;width:1200px">★★★</div>
<div class="abs section-title" style="left:0;top:3240px;width:1200px">FREQUENTLY ASKED QUESTIONS</div>
<div class="abs acc-open">
  <div class="acc-head">Why should I be concerned about legal claims?
    <svg width="18" height="18" viewBox="0 0 18 18"><circle cx="9" cy="9" r="8" fill="none" stroke="#163a78" stroke-width="1.3"/><path d="M5.5 10.5L9 7l3.5 3.5" fill="none" stroke="#163a78" stroke-width="1.3"/></svg></div>
  <p>Lorem ipsum dolor sit amet, consectetur adipiscing elit. Suspendisse varius enim in eros elementum tristique. Duis cursus, mi quis viverra ornare, eros dolor interdum nulla, ut commodo diam libero vitae erat.</p>
</div>
<div class="abs acc" style="top:3458px;height:60px"><span>Provide more details about the value of GAC's<br>contract language.</span><svg width="18" height="18" viewBox="0 0 18 18"><circle cx="9" cy="9" r="8" fill="none" stroke="#163a78" stroke-width="1.3"/><path d="M5.5 7.5L9 11l3.5-3.5" fill="none" stroke="#163a78" stroke-width="1.3"/></svg></div>
<div class="abs acc" style="top:3532px;height:71px"><span>If I'm a contractor, for example, how can an GAC<br>membership minimize legal claims against<br>my business?</span><svg width="18" height="18" viewBox="0 0 18 18"><circle cx="9" cy="9" r="8" fill="none" stroke="#163a78" stroke-width="1.3"/><path d="M5.5 7.5L9 11l3.5-3.5" fill="none" stroke="#163a78" stroke-width="1.3"/></svg></div>
<div class="abs acc" style="top:3621px;height:38px"><span>What does an GAC membership cost?</span><svg width="18" height="18" viewBox="0 0 18 18"><circle cx="9" cy="9" r="8" fill="none" stroke="#163a78" stroke-width="1.3"/><path d="M5.5 7.5L9 11l3.5-3.5" fill="none" stroke="#163a78" stroke-width="1.3"/></svg></div>
<div class="abs acc" style="top:3674px;height:38px"><span>Do you have a Referral Program?</span><svg width="18" height="18" viewBox="0 0 18 18"><circle cx="9" cy="9" r="8" fill="none" stroke="#163a78" stroke-width="1.3"/><path d="M5.5 7.5L9 11l3.5-3.5" fill="none" stroke="#163a78" stroke-width="1.3"/></svg></div>
<div class="abs faq-photo" role="img" aria-label="Judge in robe on the phone in a library office"></div>

<!-- footer -->
<div class="abs footer"></div>
<div class="abs f-brand">GAC</div>
<svg class="abs" style="left:298px;top:3866px" width="14" height="18" viewBox="0 0 14 18"><path d="M7 17s6-6.5 6-10.5A6 6 0 0 0 1 6.5C1 10.5 7 17 7 17z" fill="none" stroke="#c4121c" stroke-width="1.6"/><circle cx="7" cy="6.5" r="2" fill="#c4121c"/></svg>
<div class="abs f-address">4820 EAST CANYON RIDGE RD. SUITE 210, MESA,<br>ARIZONA 85210</div>
<svg class="abs" style="left:296px;top:3942px" width="16" height="16" viewBox="0 0 16 16"><path d="M3 1l3 3-1.5 2.5a9 9 0 0 0 5 5L12 10l3 3-2 2C7 15 1 9 1 3z" fill="none" stroke="#c4121c" stroke-width="1.6"/></svg>
<div class="abs f-phone">(480) 555-0142 / (800) 555-0199</div>
<div class="abs f-nav"><b>HOME</b><br>ABOUT<br>SERVICES<br>FAQ<br>CONTACT US</div>
<div class="abs f-legal">TERMS OF SERVICE<br>PRIVACY POLICY</div>
<div class="abs social" style="left:912px"></div>
<div class="abs social" style="left:945px"></div>
<div class="abs social" style="left:978px"></div>
<div class="abs social" style="left:1012px"></div>
<div class="abs btn-red f-btn">SCHEDULE FREE CONSULATION</div>
<div class="abs copy">Copyright© 2025 GUARDAGAINSTCLAIMS.NET | All Rights Reserved</div>

</body>
</html>
```